Tiny Meadow Product Label for Tear-Free Head-to-Toe Wash

Need a bottle label design for a new line of natural products targeting infants and children. Products are Pediatrician-developed and paraben-free, sulfate-free, fragrance-free, and cruelty-free. Design should be clean and have a high-end feel to it. Will need other product labels in Tiny Meadow line designed as well in upcoming projects.

Target Market(s)

Newborn to young elementary age children and their parents

Industry/Entity Type

Cosmetics/Beauty

Font styles to use
Other font styles liked:
• Brand fonts are Jost and Sonorous

Colors

Designer to choose colors to be used in the design.

Requirements
Must have
• Tiny Meadow logo, Pediatrician Developed logo, and a clean high-end feel to it. The label must fit the specialty bottle we will be using (label measurements and diagram will be provided) for the front and back of bottle only (NOT the side labels). It must include our list of ingredients (will provide once designer selected).
Nice to have
• Should stand out on the shelf of other baby products due to it's clean simplicity and high-end feel
Should not have
• too much of a "kiddie" feel to it (targeting the parents not the kids)

```html
<!DOCTYPE html>
<html lang="en">
<head>
<meta charset="UTF-8">
<title>Tiny Meadow – Tear-Free Head-to-Toe Wash Labels</title>
<link href="https://fonts.googleapis.com/css2?family=Arimo:ital,wght@0,400;0,700;1,400;1,700&display=swap" rel="stylesheet">
<style>
  :root {
    --page-bg: #ecebe8;
    --label-bg: #fbfafa;
    --ink: #1c1c1c;
    --gold: #9a7634;
    --sand: #cfc5ba;
    --sand-light: #d9d0c6;
    --badge-line: #e6ded4;
    --deco: #f1eee8;
  }
  * { margin: 0; padding: 0; box-sizing: border-box; }
  html, body {
    width: 1200px; height: 1200px; overflow: hidden;
    background: var(--page-bg);
    font-family: "Arimo", Arial, sans-serif;
    color: var(--ink);
  }
  .label {
    position: absolute; top: 270px;
    width: 460px; height: 660px;
  }
  .label--front { left: 90px; }
  .label--back { left: 650px; }
  .label-shape { position: absolute; inset: 0; }

  /* Front */
  .brand-mark {
    position: absolute; left: 127px; top: 50px;
    width: 204px; height: 204px;
    border: 2px solid var(--ink); border-radius: 50%;
    display: flex; align-items: center; justify-content: center;
  }
  .brand-name {
    font-size: 22px; font-weight: 700; letter-spacing: 2px;
    color: var(--ink); text-transform: uppercase;
  }
  .product-title {
    position: absolute; left: 0; right: 0; top: 300px;
    text-align: center; font-size: 28px; font-weight: 700; line-height: 33px;
  }
  .product-tagline {
    position: absolute; left: 0; right: 0; top: 370px;
    text-align: center; font-size: 16px; font-style: italic; color: var(--gold);
  }
  .net-weight {
    position: absolute; left: 0; right: 0; top: 610px;
    text-align: center; font-size: 19px; font-weight: 700;
  }

  /* Back */
  .back-copy {
    position: absolute; left: 62px; width: 336px; top: 103px;
    font-size: 17px; line-height: 23.5px;
  }
  .back-copy p { text-align: justify; text-align-last: center; }
  .section-heading {
    text-align: center; font-size: 22px; font-weight: 700; font-style: italic;
    color: var(--sand-light); margin: 10px 0 6px;
  }
  .maker {
    position: absolute; left: 62px; top: 540px;
    font-size: 17px; line-height: 23.5px;
  }
  .maker-heading { font-weight: 700; font-style: italic; color: var(--sand-light); }
  .deco-area {
    position: absolute; left: 200px; top: 40px; width: 260px; height: 300px;
    border-radius: 50% 0 0 50%;
    background: radial-gradient(circle at 60% 45%, var(--deco), rgba(241,238,232,0) 70%);
  }
</style>
</head>
<body>

<section class="label label--front">
  <svg class="label-shape" width="460" height="660" viewBox="0 0 460 660">
    <path d="M0,100 Q0,60 40,45 Q230,-20 420,45 Q460,60 460,100 L460,660 L0,660 Z" fill="var(--label-bg)"/>
    <path d="M0,413 C20,520 120,560 230,540 C330,520 400,470 460,452 L460,660 L0,660 Z" fill="var(--sand)"/>
    <g fill="none" stroke="var(--badge-line)" stroke-width="2">
      <circle cx="84" cy="496" r="29"/>
      <circle cx="162" cy="502" r="29"/>
      <circle cx="237" cy="490" r="29"/>
      <circle cx="311" cy="466" r="29"/>
    </g>
  </svg>
  <div class="brand-mark"><span class="brand-name">Tiny Meadow</span></div>
  <h1 class="product-title">Tear-Free<br>Head-to-Toe Wash</h1>
  <p class="product-tagline">Naturally formulated for delicate skin</p>
  <p class="net-weight">Net wt: 73 mL/2,43 fl.oz</p>
</section>

<section class="label label--back">
  <svg class="label-shape" width="460" height="660" viewBox="0 0 460 660">
    <path d="M0,100 Q0,60 40,45 Q230,-20 420,45 Q460,60 460,100 L460,660 L0,660 Z" fill="var(--label-bg)"/>
    <circle cx="365" cy="570" r="30" fill="none" stroke="var(--badge-line)" stroke-width="2"/>
  </svg>
  <div class="deco-area" role="img" aria-label="Faint line-art brand decoration"></div>
  <div class="back-copy">
    <p>A gentle, all-in-one cleanser made with natural ingredients to protect and nourish baby’s delicate hair and skin. Pediatrician-developed and suitable for daily use from newborn onwards.</p>
    <h2 class="section-heading">Directions:</h2>
    <p>Dispense a small amount into hands or washcloth. Gently massage into wet hair and skin. Rinse thoroughly. Avoid contact with eyes.</p>
    <h2 class="section-heading">Ingredients:</h2>
    <p>Aqua, Glycerin, Decyl Glucoside, Sodium Lauroyl Lactylate, Coco-Glucoside, Glyceryl Oleate, Xanthan Gum, Sodium Benzoate, Citric Acid. (Full list to be finalized.)</p>
  </div>
  <div class="maker">
    <p class="maker-heading">Manufactured for</p>
    <p>Tiny Meadow Co.</p>
    <p>tinymeadow.com/Made in USA</p>
  </div>
</section>

</body>
</html>
```